Business cards for Norwegian software consultancy business

We are in need of business cards for our Norwegian consultancy company.
“Valto Brindex AS” specializes in software development, architecture and agile methodology, providing mostly on-site services at customers.
The cards should reflect a certain level of business professionalism with an elegant touch, while paying tribute to our modern and technological heritage. Our logo should be featured, as well as room for basic information about the cardholder and legal information of the company (company name, address and VAT number).
We would like our cards to reflect that we are a modern consulting company. It should present a professional image that people will remember. The texture and color pallette should reflect our professionalism and reliability, so we prefer a light color pallette with colors such as gray, white, blue and black. The number of colors used should however not be overwhelming, with the text being distinct and readable.
We are open to untraditional layouts and playful designs as long as they communicate the intent stated above.
You could also take a look at our website http://www.brindex.no for input on our visual profile.
Our logo is attached in the form of vectors and rasterized PNG. Please comment if you would like the black-white and/or inverted versions as well.
Industry/Entity Type
Architecture
Contact Information for Business Card
Company information:
Valto Brindex AS
Kvernlia 14, 3170 Sem
482 71 519
info@brindex.no
www.brindex.no
Employee information:
Full name
Title
Email
Phone
Font styles to use
Look and feel

```html
<!DOCTYPE html>
<html lang="no">
<head>
<meta charset="utf-8">
<title>Valto Brindex AS – Business Card</title>
<link href="https://fonts.googleapis.com/css2?family=Lato:wght@400;700&display=swap" rel="stylesheet">
<style>
  :root {
    --backdrop: #d9d9d9;
    --paper: #fbfbfb;
    --paper-shade: #f1f1f1;
    --ink: #6b6b6b;
    --ink-dark: #3a3a3a;
    --band: #2f3131;
    --band-light: #4a4c4c;
    --band-text: #f2f2f2;
    --accent: #6fa3d2;
  }
  * { margin: 0; padding: 0; box-sizing: border-box; }
  html, body {
    width: 1200px; height: 900px; overflow: hidden;
    background: var(--backdrop);
    font-family: "Lato", sans-serif;
  }
  .card {
    position: absolute; left: 100px; top: 164px;
    width: 1000px; height: 572px;
    background: linear-gradient(135deg, var(--paper) 0%, var(--paper-shade) 100%);
    box-shadow: 0 10px 30px rgba(0,0,0,0.18);
    overflow: hidden;
  }
  .brand {
    position: absolute; left: 360px; top: 70px;
    display: flex; align-items: center; gap: 22px;
  }
  .brand-mark {
    width: 54px; height: 54px; background: var(--accent);
  }
  .brand-name {
    font-size: 46px; font-weight: 400; letter-spacing: 6px;
    color: var(--ink-dark);
  }
  .company {
    position: absolute; left: 60px; top: 170px;
    color: var(--ink); font-size: 25px; line-height: 1.3;
  }
  .company-name { font-weight: 700; }
  .contacts {
    position: absolute; left: 60px; top: 300px;
    list-style: none; color: var(--ink-dark); font-size: 25px;
  }
  .contacts li { display: flex; align-items: center; gap: 18px; height: 32px; }
  .contacts svg { width: 20px; height: 20px; fill: none; stroke: var(--accent); stroke-width: 1.8; }
  .band {
    position: absolute; left: 0; top: 410px; width: 1000px; height: 162px;
  }
  .holder {
    position: absolute; left: 60px; top: 500px;
    color: var(--band-text); font-size: 30px;
    display: flex; align-items: center; gap: 12px;
  }
  .holder-title {
    font-size: 20px; letter-spacing: 1px;
    border-left: 2px solid var(--band-text); padding-left: 12px;
  }
  .website {
    position: absolute; right: 70px; top: 440px;
    color: var(--band-text); font-size: 22px; letter-spacing: 6px;
  }
</style>
</head>
<body>
  <article class="card">
    <div class="brand">
      <span class="brand-mark"></span>
      <span class="brand-name">VALTO BRINDEX</span>
    </div>

    <address class="company" style="font-style:normal">
      <div class="company-name">Valto Brindex AS</div>
      <div>Kvernlia 14</div>
      <div>3170 Sem</div>
    </address>

    <ul class="contacts">
      <li>
        <svg viewBox="0 0 20 20"><path d="M5 2 L8 6 L6 8 Q8 12 12 14 L14 12 L18 15 L16 18 Q8 18 2 6 Z"/></svg>
        482 71 519
      </li>
      <li>
        <svg viewBox="0 0 20 20"><rect x="5" y="2" width="10" height="6"/><rect x="2" y="8" width="16" height="7"/><rect x="5" y="13" width="10" height="5"/></svg>
        482 71 520
      </li>
      <li>
        <svg viewBox="0 0 20 20"><rect x="2" y="4" width="16" height="12"/><path d="M2 4 L10 11 L18 4"/></svg>
        ehalvorsen@brindex.no
      </li>
    </ul>

    <svg class="band" viewBox="0 0 1000 162" preserveAspectRatio="none">
      <defs>
        <linearGradient id="band-fade" x1="0" x2="1" y1="0" y2="0">
          <stop offset="0" stop-color="var(--band-light)"/>
          <stop offset="0.3" stop-color="var(--band)"/>
          <stop offset="1" stop-color="var(--band)"/>
        </linearGradient>
      </defs>
      <path d="M0 14 H38 L48 0 L58 14 H1000 V162 H0 Z" fill="url(#band-fade)"/>
    </svg>

    <div class="holder">
      <span class="holder-name">Eirik Halvorsen</span>
      <span class="holder-title">DIRECTOR</span>
    </div>
    <div class="website">www.brindex.no</div>
  </article>
</body>
</html>
```